Brand Identity Stationary Package

Hello I'm looking for a full branding package for my Property Management Company. I have a logo but looking to have the following
Business Card
Email signature
Facebook cover photo
Letterhead (word.doc)
#10 Envelope
Pocket Folder - link to 9x12 pocket folder design specs https://www.printorbit-example.ca/marketing-materials/presentation-folders
would like everything to match and be brand identifiable. The company looks after residential properties/apartments and some commercial properties. Attached is a zip of the files.
For Business Card
Name: Gareth Lindqvist
Position: Operations Manager
Number: 1 (555) 384-2917
Email: Gareth@harborkey-example.ca
Website: Harborkey-example.ca
Property Management

```html
<!DOCTYPE html>
<html lang="en">
<head>
<meta charset="utf-8">
<title>Harborkey Property Management — #10 Envelope</title>
<link href="https://fonts.googleapis.com/css2?family=Source+Sans+3:wght@400;600&display=swap" rel="stylesheet">
<style>
  :root {
    --brand-green: #80a641;
    --ink: #111111;
    --paper: #f7f6f6;
    --backdrop: #d4d3d3;
    --white: #ffffff;
  }
  * { margin: 0; padding: 0; box-sizing: border-box; }
  html, body {
    width: 1200px;
    height: 1050px;
    overflow: hidden;
    background: var(--backdrop);
    font-family: "Source Sans 3", "Helvetica Neue", Arial, sans-serif;
  }
  .canvas {
    position: relative;
    width: 1200px;
    height: 1050px;
  }
  .envelope {
    position: absolute;
    left: 145px;
    width: 910px;
    height: 390px;
    background: var(--paper);
    overflow: hidden;
  }
  .envelope--back { top: 105px; }
  .envelope--front { top: 555px; }

  .envelope__art {
    position: absolute;
    inset: 0;
    width: 910px;
    height: 390px;
  }

  .flap-brand {
    position: absolute;
    top: 32px;
    left: 0;
    width: 910px;
    text-align: center;
    color: var(--white);
  }
  .brand-name {
    display: block;
    font-weight: 600;
    font-size: 46px;
    line-height: 1;
    letter-spacing: 4px;
  }
  .brand-tagline {
    display: block;
    font-weight: 600;
    font-size: 11px;
    letter-spacing: 8.2px;
    margin-top: 10px;
  }

  .sender {
    position: absolute;
    left: 52px;
    top: 62px;
    color: var(--ink);
  }
  .sender .brand-name {
    font-size: 38px;
    letter-spacing: 4.4px;
  }
  .sender .brand-tagline {
    font-size: 9.5px;
    letter-spacing: 7.1px;
    margin-top: 8px;
  }

  .contact-list {
    list-style: none;
    margin-top: 36px;
  }
  .contact-item {
    display: flex;
    align-items: center;
    height: 26px;
    font-size: 20px;
    color: var(--ink);
  }
  .contact-icon {
    width: 16px;
    height: 16px;
    margin-right: 12px;
    flex: none;
  }
</style>
</head>
<body>
<main class="canvas">

  <section class="envelope envelope--back" aria-label="Envelope back with flap">
    <svg class="envelope__art" viewBox="0 0 910 390" aria-hidden="true">
      <path d="M0 0 H910 L887 90 Q874 131 834 131 H76 Q36 131 23 90 Z" fill="var(--brand-green)"/>
    </svg>
    <div class="flap-brand">
      <span class="brand-name">HARBORKEY</span>
      <span class="brand-tagline">PROPERTY MANAGEMENT</span>
    </div>
  </section>

  <section class="envelope envelope--front" aria-label="Envelope front with return address">
    <svg class="envelope__art" viewBox="0 0 910 390" aria-hidden="true">
      <path d="M0 350 C90 308 240 290 420 312 C520 324 600 356 720 358 C820 360 880 340 910 316 V390 H0 Z" fill="var(--brand-green)"/>
      <path d="M564 339 C700 345 850 330 910 286 V304 C860 340 760 350 564 339 Z" fill="var(--ink)"/>
    </svg>

    <div class="sender">
      <span class="brand-name">HARBORKEY</span>
      <span class="brand-tagline">PROPERTY MANAGEMENT</span>

      <ul class="contact-list">
        <li class="contact-item">
          <svg class="contact-icon" viewBox="0 0 16 16" aria-hidden="true">
            <path d="M1 6 Q8 1 15 6 L13 7.5 L11 6.5 L11 5 Q8 4 5 5 L5 6.5 L3 7.5 Z" fill="var(--brand-green)"/>
            <rect x="3" y="8" width="10" height="6" rx="1" fill="var(--brand-green)"/>
          </svg>
          1 (555) 384-2917
        </li>
        <li class="contact-item">
          <svg class="contact-icon" viewBox="0 0 16 16" aria-hidden="true">
            <rect x="0.5" y="3" width="15" height="10" fill="var(--brand-green)"/>
            <path d="M0.5 3 L8 9 L15.5 3" fill="none" stroke="var(--paper)" stroke-width="1.3"/>
          </svg>
          Gareth@harborkey-example.ca
        </li>
        <li class="contact-item">
          <svg class="contact-icon" viewBox="0 0 16 16" aria-hidden="true">
            <circle cx="8" cy="8" r="7.5" fill="var(--brand-green)"/>
            <ellipse cx="8" cy="8" rx="3" ry="7.5" fill="none" stroke="var(--paper)" stroke-width="1"/>
            <path d="M0.5 8 H15.5" stroke="var(--paper)" stroke-width="1"/>
          </svg>
          www.Harborkey-example.ca
        </li>
      </ul>
    </div>
  </section>

</main>
</body>
</html>
```